We Buy Houses Postcard Design

Harborline Asset Partners is one of Baltimore‘s top real estate investing groups because we treat buyers and sellers like real people; not like numbers on a spreadsheet. We specialize in buying distressed properties including multi-family, commercial, retail, single family, and bank REO’s from sellers who need to sell fast. Our website is www.harborlineassetpartners.com. Our phone number is (555) 274-1916. Both need to be on the card. Front and back sides are to be printed. Front full color, back black and white. We want our logo on the design somewhere. The logo can be found on the website. If you need the original files ask me for them. See attached as examples. Return address should be 587 W Tessaly Ave, Suite 319, Baltimore, MD 21209. My name is Marcus. Address label is 1" x 2-5/8". Please leave room for it and postage on the back side.

Industry/Entity Type

Real Estate

```html
<!DOCTYPE html>
<html lang="en">
<head>
<meta charset="utf-8">
<title>Harborline Asset Partners – We Buy Houses Postcard</title>
<link rel="stylesheet" href="https://fonts.googleapis.com/css2?family=Arimo:wght@700&family=Courier+Prime:wght@400;700&family=Great+Vibes&display=swap">
<style>
  :root {
    --brand-red: #e8101f;
    --paper: #ffffff;
    --ink: #1a1a1a;
    --highlight: #ffe500;
    --backdrop: #d6d6d6;
  }
  * { margin: 0; padding: 0; box-sizing: border-box; }
  html, body { width: 1200px; height: 900px; overflow: hidden; }
  body { background: var(--backdrop); position: relative; }

  .postcard {
    position: absolute;
    width: 600px;
    height: 400px;
    background: var(--paper);
    box-shadow: 0 2px 8px rgba(0,0,0,0.18);
  }

  /* Front side */
  .postcard--front { left: 60px; top: 40px; }
  .front-headline {
    position: absolute;
    left: 28px;
    top: 18px;
    font-family: "Arimo", Arial, sans-serif;
    font-weight: 700;
    font-size: 112px;
    line-height: 108px;
    letter-spacing: 6px;
    color: var(--brand-red);
  }
  .front-tagline {
    position: absolute;
    left: 30px;
    top: 240px;
    font-family: "Arimo", Arial, sans-serif;
    font-weight: 700;
    font-size: 27px;
    letter-spacing: 2px;
    color: var(--brand-red);
  }
  .front-phone-band {
    position: absolute;
    left: 18px;
    right: 18px;
    top: 284px;
    height: 96px;
    background: var(--brand-red);
    display: flex;
    align-items: center;
    justify-content: center;
    font-family: "Arimo", Arial, sans-serif;
    font-weight: 700;
    font-size: 66px;
    letter-spacing: 3px;
    color: var(--paper);
  }

  /* Back side */
  .postcard--back {
    left: 540px;
    top: 460px;
    font-family: "Courier Prime", "Courier New", monospace;
    font-size: 11px;
    line-height: 15px;
    color: var(--ink);
  }
  .back-brand {
    position: absolute;
    left: 40px;
    top: 20px;
    font-family: "Courier Prime", "Courier New", monospace;
    font-weight: 700;
    font-size: 13px;
    color: var(--ink);
  }
  .back-intro { position: absolute; left: 40px; top: 48px; }
  .back-intro mark { background: var(--highlight); color: var(--ink); padding: 0 2px; }
  .offer-box {
    position: absolute;
    left: 34px;
    top: 82px;
    width: 330px;
    padding: 5px 8px;
    border: 2px solid var(--brand-red);
    list-style: none;
  }
  .offer-box li::before { content: "- "; }
  .back-message { position: absolute; left: 40px; top: 160px; width: 545px; }
  .signature {
    position: absolute;
    left: 44px;
    top: 210px;
    font-family: "Great Vibes", cursive;
    font-size: 22px;
    color: var(--ink);
  }
  .return-address { position: absolute; left: 40px; top: 244px; font-size: 10px; line-height: 13px; }
  .return-address .phone { font-family: "Arimo", Arial, sans-serif; font-weight: 700; font-size: 12px; line-height: 17px; }
  .urgent-band {
    position: absolute;
    left: 350px;
    top: 312px;
    width: 230px;
    height: 56px;
    background: var(--brand-red);
    display: flex;
    align-items: center;
    justify-content: center;
    font-family: "Arimo", Arial, sans-serif;
    font-weight: 700;
    font-size: 20px;
    letter-spacing: 3px;
    color: var(--paper);
  }
</style>
</head>
<body>

  <section class="postcard postcard--front">
    <h1 class="front-headline">WE BUY<br>HOUSES</h1>
    <p class="front-tagline">ANY CONDITION - FAST CLOSING</p>
    <p class="front-phone-band">(555) 274-1916</p>
  </section>

  <section class="postcard postcard--back">
    <p class="back-brand">Harborline Asset Partners</p>
    <p class="back-intro">My name is Marcus. <mark>We are interested in buying your house!</mark><br>We offer...</p>
    <ul class="offer-box">
      <li>CASH for your house "AS-IS"</li>
      <li>No inspections or contingencies</li>
      <li>Fast and flexible closing</li>
      <li>No need to fix or clean out your home</li>
    </ul>
    <p class="back-message">
      If you're interested, please contact us. There are never any obligations.<br>
      We like to think the worst case is you spend a few minutes on the phone with us.<br>
      We look forward to hearing from you!
    </p>
    <p class="signature">Marcus</p>
    <address class="return-address">
      Harborline Asset Partners<br>
      www.harborlineassetpartners.com<br>
      587 W Tessaly Ave, Suite 319, Baltimore, MD 21209.<br>
      <span class="phone">(555) 274-1916</span>
    </address>
    <p class="urgent-band">URGENT NOTICE</p>
  </section>

</body>
</html>
```